Software Development Consulting Company Needs Business Card Design

We need a new business card design for our consultants at Kestrel Works (kestrelworks.example). We are a small firm that provides high-end software development and methodology consulting to medium to large enterprise IT organizations.

Our logo uses Futura for the font and we would like to stick with navy blue and canary yellow for the logo colors. Attached are normal and reversed versions of our logos in illustrator format.
Updates

Hi Everyone, Thank yo very much for your amazing design ideas. I have created a poll for this project and our employees will be voting on the design they wish to use. We will be making a decision this Wednesday (October 22nd). Thanks again, Dale Hartwick

Industry/Entity Type

Business

```html
<!DOCTYPE html>
<html lang="en">
<head>
<meta charset="utf-8">
<title>Kestrel Works — Business Card</title>
<link rel="stylesheet" href="https://fonts.googleapis.com/css2?family=Jost:wght@400;500&family=Open+Sans:wght@400;600&display=swap">
<style>
  :root {
    --navy: #1d4a6e;
    --canary: #f2e21c;
    --white: #ffffff;
    --ink-grey: #6b6f75;
    --stage: #eceef2;
    --card-shadow: rgba(20, 30, 45, 0.18);
  }
  * { box-sizing: border-box; margin: 0; padding: 0; }
  html, body {
    width: 1200px; height: 980px; overflow: hidden;
    background: var(--stage);
    font-family: "Open Sans", Arial, sans-serif;
  }
  .sheet {
    position: relative; width: 1200px; height: 980px;
    display: flex; flex-direction: column; align-items: center;
    justify-content: center; gap: 60px;
  }
  .card {
    position: relative; width: 700px; height: 400px;
    border-radius: 34px; overflow: hidden;
    box-shadow: 0 10px 28px var(--card-shadow);
  }

  /* Wordmark */
  .wordmark {
    display: flex; align-items: center; gap: 16px;
    font-family: "Jost", "Futura", sans-serif; font-weight: 500;
    letter-spacing: 0.16em; text-transform: uppercase;
  }
  .wordmark__dot {
    width: 34px; height: 34px; border-radius: 50%;
    border: 4px solid currentColor;
  }

  /* Front */
  .card--front { background: var(--white); }
  .front__logo {
    position: absolute; top: 44px; left: 0; right: 0;
    display: flex; justify-content: center;
  }
  .front__logo .wordmark { color: var(--navy); font-size: 40px; }
  .front__band {
    position: absolute; left: 0; right: 0; top: 128px; height: 186px;
    background: var(--navy);
    border-top: 3px solid var(--canary);
    border-bottom: 3px solid var(--canary);
    display: flex; align-items: center; justify-content: center;
    color: var(--white);
  }
  .identity {
    text-align: right; padding-right: 26px; margin-right: 26px;
    border-right: 1.5px solid rgba(255,255,255,0.7);
    line-height: 1.35;
  }
  .identity__name { font-weight: 600; font-size: 24px; }
  .identity__title { font-size: 17px; }
  .identity__place { font-size: 16px; margin-top: 2px; }
  .contact { list-style: none; font-size: 17px; line-height: 1.9; }
  .contact li { display: flex; align-items: center; gap: 10px; }
  .contact svg { width: 16px; height: 16px; flex: none; }
  .front__footer {
    position: absolute; left: 48px; bottom: 30px;
    font-size: 26px; color: var(--navy); font-weight: 600;
  }
  .front__footer span { font-weight: 400; font-size: 20px; color: var(--ink-grey); }

  /* Back */
  .card--back {
    background: var(--navy); color: var(--white);
    display: flex; flex-direction: column; align-items: center; justify-content: center;
    gap: 46px;
  }
  .card--back .wordmark { font-size: 44px; }
  .back__url { font-size: 20px; letter-spacing: 0.22em; }
</style>
</head>
<body>
<main class="sheet">

  <section class="card card--front" aria-label="Business card front">
    <div class="front__logo">
      <div class="wordmark"><span class="wordmark__dot"></span>Kestrel Works</div>
    </div>

    <div class="front__band">
      <div class="identity">
        <p class="identity__name">Your Name</p>
        <p class="identity__title">Title</p>
        <p class="identity__place">Lakeport + Millbrook, IL</p>
      </div>
      <ul class="contact">
        <li>
          <svg viewBox="0 0 16 16" aria-hidden="true"><circle cx="8" cy="8" r="7.2" fill="none" stroke="#fff" stroke-width="1.2"/><path d="M5.5 4.5l1.4-.3.8 1.8-.9.8c.4 1 1.1 1.8 2.1 2.2l.8-.9 1.8.8-.3 1.4c-3 .3-6-2.7-5.7-5.8z" fill="#fff"/></svg>
          012-345-6789
        </li>
        <li>
          <svg viewBox="0 0 16 16" aria-hidden="true"><rect x="1.5" y="3.5" width="13" height="9" rx="1" fill="none" stroke="#fff" stroke-width="1.4"/><path d="M1.5 4l6.5 5 6.5-5" fill="none" stroke="#fff" stroke-width="1.4"/></svg>
          info@kestrelworks.example
        </li>
        <li>
          <svg viewBox="0 0 16 16" aria-hidden="true"><g fill="none" stroke="#fff" stroke-width="1.1"><circle cx="8" cy="8" r="6.8"/><ellipse cx="8" cy="8" rx="3" ry="6.8"/><path d="M1.2 8h13.6M2.4 4.6h11.2M2.4 11.4h11.2"/></g></svg>
          www.kestrelworks.example
        </li>
      </ul>
    </div>

    <p class="front__footer">Your Name, <span>Title</span></p>
  </section>

  <section class="card card--back" aria-label="Business card back">
    <div class="wordmark"><span class="wordmark__dot"></span>Kestrel Works</div>
    <p class="back__url">www.kestrelworks.example</p>
  </section>

</main>
</body>
</html>
```